Business Card Design - VNT (company name)

Over 20 years of progressive technology design, migration and management experience that drives business objectives and streamlines operations. Continuously challenge conventions to meet and exceed business security, availability and functionality requirements. Maintain exceptional vendor relationships to ensure ongoing knowledge of emerging products and to secure preferred service agreements. Recruit and utilize top talent and foster a collegial environment that advances innovation and performance excellence. design logo using 3 arrows of different colors green, gold, blue

Industry/Entity Type

Progressive

Contact Information for Business Card

Martin K. Osgood
IT Strategist / Consultant

626.583.2907 MOsgood@vntosgood.example 4817 Brenning Court Pasadena, CA 91104

Colors
0255a3
f37122
fece3e

Requirements
Must have
• Note NEW EMAIL ADDRESS
• MOsgood@vntosgood.example
• NOTE NEW ORDER of the work I do.
• Infrastructure – Systems – Cybersecurity
Nice to have
• main color should be orange

```html
<!DOCTYPE html>
<html lang="en">
<head>
<meta charset="utf-8">
<title>VNT Business Card</title>
<link rel="stylesheet" href="https://fonts.googleapis.com/css2?family=Open+Sans:ital,wght@0,300;0,400;0,700;1,300&display=swap">
<style>
  :root {
    --brand-blue: #0255a3;
    --brand-orange: #f37122;
    --brand-gold: #fece3e;
    --ink: #2b2b2b;
    --ink-soft: #555555;
    --card: #ffffff;
    --backdrop: #ecebe8;
  }
  * { margin: 0; padding: 0; box-sizing: border-box; }
  html, body {
    width: 1200px;
    height: 873px;
    overflow: hidden;
    background: var(--backdrop);
    font-family: "Open Sans", Arial, sans-serif;
  }
  .canvas {
    position: relative;
    width: 1200px;
    height: 873px;
    display: flex;
    align-items: center;
    justify-content: center;
    gap: 60px;
  }
  .card {
    position: relative;
    width: 520px;
    height: 297px;
    background: var(--card);
    box-shadow: 0 4px 14px rgba(0,0,0,0.12);
    overflow: hidden;
  }
  .card-front .color-bands {
    position: absolute;
    inset: 0;
    width: 100%;
    height: 100%;
  }
  .holder-name {
    position: absolute;
    left: 160px;
    top: 48px;
    font-size: 27px;
    font-weight: 300;
    color: var(--ink);
    letter-spacing: 0.2px;
    white-space: nowrap;
  }
  .holder-title {
    position: absolute;
    left: 162px;
    top: 86px;
    font-size: 11px;
    font-style: italic;
    font-weight: 300;
    color: var(--ink-soft);
    white-space: nowrap;
  }
  .divider {
    position: absolute;
    left: 268px;
    top: 112px;
    width: 2px;
    height: 64px;
    background: var(--brand-orange);
  }
  .contact {
    position: absolute;
    left: 282px;
    top: 116px;
    font-size: 18px;
    font-weight: 700;
    color: var(--ink);
    line-height: 28px;
    white-space: nowrap;
  }
  .contact .email { font-size: 13px; }
  .address {
    position: absolute;
    left: 34px;
    bottom: 16px;
    font-size: 19px;
    font-weight: 400;
    color: var(--card);
    letter-spacing: 0.3px;
    white-space: nowrap;
  }
  .card-back {
    display: flex;
    flex-direction: column;
    align-items: center;
    justify-content: center;
  }
  .brand {
    display: flex;
    align-items: center;
    gap: 14px;
    margin-top: 10px;
  }
  .brand-dot {
    width: 44px;
    height: 44px;
    border-radius: 50%;
    background: var(--brand-orange);
  }
  .brand-name {
    font-size: 34px;
    font-weight: 400;
    color: var(--brand-blue);
    letter-spacing: 2px;
  }
  .services {
    margin-top: 46px;
    font-size: 18px;
    font-weight: 300;
    color: var(--ink);
    white-space: nowrap;
  }
</style>
</head>
<body>
<main class="canvas">
  <section class="card card-front">
    <svg class="color-bands" viewBox="0 0 520 297" preserveAspectRatio="none" aria-hidden="true">
      <path d="M0 0 H70 C110 90 150 160 200 222 L0 222 Z" fill="var(--brand-blue)"/>
      <path d="M0 0 H40 C80 95 120 165 160 222 L0 222 Z" fill="var(--brand-orange)"/>
      <path d="M300 222 C380 212 450 196 520 176 V222 Z" fill="var(--brand-gold)"/>
      <rect x="0" y="222" width="520" height="75" fill="var(--brand-orange)"/>
    </svg>
    <h1 class="holder-name">Martin K. Osgood</h1>
    <p class="holder-title">IT Strategist / Consultant</p>
    <span class="divider"></span>
    <div class="contact">
      <p class="phone">626.583.2907</p>
      <p class="email">MOsgood@vntosgood.example</p>
    </div>
    <p class="address">4817 Brenning Court - Pasadena CA 91104</p>
  </section>

  <section class="card card-back">
    <div class="brand">
      <span class="brand-dot"></span>
      <span class="brand-name">VNT</span>
    </div>
    <p class="services">Infrastructure - Systems - Cybersecurity</p>
  </section>
</main>
</body>
</html>
```